Real Estate Brokerage Stationery Designs

I am looking to have presentation folders with business card slots on both sides along with pockets on both sides. I've attached logos, website colors along with current business card designs.

I am looking for envelope designs both big and small. Possibly new business card designs, notepad templates for big and small notepads. Letterhead designs. Pop socket designs. Realtors name badge designs.

www.brightholdrealty.example

```html
<!DOCTYPE html>
<html lang="en">
<head>
<meta charset="utf-8">
<title>Brighthold Realty Stationery</title>
<link rel="stylesheet" href="https://fonts.googleapis.com/css2?family=Open+Sans:wght@400;600&family=Tinos:wght@400&display=swap">
<style>
  :root {
    --backdrop: #a9a8a9;
    --brand-blue: #0057a8;
    --band-grey: #b3b3b5;
    --paper-light: #fbfbfb;
    --paper-dark: #e2e2e3;
    --ink: #555;
    --ink-soft: #666;
  }
  * { margin: 0; padding: 0; box-sizing: border-box; }
  html, body { width: 1200px; height: 871px; overflow: hidden; background: var(--backdrop); }
  .canvas { position: relative; width: 1200px; height: 871px; }

  .sheet {
    position: absolute;
    background: linear-gradient(100deg, var(--paper-light) 0%, var(--paper-dark) 100%);
    box-shadow: 0 1px 4px rgba(0,0,0,.25);
    overflow: hidden;
  }
  .brand-band { position: absolute; left: 0; right: 0; bottom: 0; height: 10px; }
  .brand-band svg { display: block; width: 100%; height: 100%; }

  .wordmark {
    font-family: "Open Sans", sans-serif;
    font-weight: 600;
    color: var(--brand-blue);
    line-height: 1.1;
    display: flex;
    align-items: center;
    gap: 6px;
  }
  .wordmark .mark-square { width: 12px; height: 12px; background: var(--brand-blue); flex: none; }

  /* Envelope front */
  .envelope-front { left: 54px; top: 216px; width: 560px; height: 256px; }
  .envelope-front .wordmark { position: absolute; left: 36px; top: 66px; font-size: 17px; }
  .return-address {
    position: absolute; left: 20px; top: 128px; width: 148px;
    font-family: "Open Sans", sans-serif; font-size: 7px; line-height: 9.5px;
    color: var(--ink); text-align: center;
  }

  /* Envelope back */
  .envelope-back { left: 54px; top: 500px; width: 560px; height: 255px; }
  .envelope-flap { position: absolute; left: 0; top: 0; width: 560px; height: 94px; }
  .envelope-flap svg { display: block; }
  .envelope-back .wordmark {
    position: absolute; left: 0; right: 0; top: 34px; justify-content: center;
    color: #fff; font-size: 16px;
  }
  .envelope-back .wordmark .mark-square { background: #fff; }

  /* Letterhead */
  .letterhead { left: 639px; top: 57px; width: 521px; height: 735px; }
  .letterhead .wordmark { position: absolute; left: 44px; top: 70px; font-size: 17px; }
  .contact-block {
    position: absolute; left: 374px; top: 42px;
    font-family: "Open Sans", sans-serif; font-size: 6.6px; line-height: 10px; color: var(--ink);
  }
  .contact-block .address { margin-bottom: 4px; }
  .contact-list { list-style: none; }
  .contact-list li { display: flex; align-items: center; gap: 5px; }
  .contact-list svg { width: 7px; height: 7px; flex: none; }

  .letter {
    position: absolute; left: 47px; top: 180px; width: 431px;
    font-family: "Tinos", serif; color: var(--ink-soft);
  }
  .letter .date { font-size: 9.5px; }
  .letter .recipient { margin-top: 24px; font-size: 9.5px; line-height: 12px; }
  .letter .body { margin-top: 20px; font-size: 7.6px; line-height: 12px; text-align: justify; }
  .letter .body p + p { margin-top: 12px; }
  .signature {
    position: absolute; left: 47px; top: 530px; width: 100px; height: 40px;
    background: linear-gradient(90deg, rgba(120,120,120,.12), rgba(120,120,120,.04));
    border-radius: 4px;
  }
</style>
</head>
<body>
<div class="canvas">

  <section class="sheet envelope-front" aria-label="Envelope front">
    <div class="wordmark"><span class="mark-square"></span>Brighthold Realty</div>
    <p class="return-address">2400 Harbor Point Ave, Suite 310,<br>Lakemont, FL 33900</p>
    <div class="brand-band">
      <svg viewBox="0 0 560 10" preserveAspectRatio="none">
        <rect width="560" height="10" fill="var(--band-grey)"/>
        <polygon points="0,0 330,0 322,10 0,10" fill="var(--brand-blue)"/>
      </svg>
    </div>
  </section>

  <section class="sheet envelope-back" aria-label="Envelope back">
    <div class="envelope-flap">
      <svg width="560" height="94" viewBox="0 0 560 94">
        <path d="M0,0 H560 L548,58 Q541,94 505,94 H55 Q19,94 12,58 Z" fill="var(--brand-blue)"/>
      </svg>
    </div>
    <div class="wordmark"><span class="mark-square"></span>Brighthold Realty</div>
  </section>

  <section class="sheet letterhead" aria-label="Letterhead">
    <div class="wordmark"><span class="mark-square"></span>Brighthold Realty</div>

    <div class="contact-block">
      <p class="address">2400 Harbor Point Ave, Suite 310,<br>Lakemont, FL 33900</p>
      <ul class="contact-list">
        <li><svg viewBox="0 0 8 8"><path d="M1,3 Q4,0 7,3 L6,4 L5,3 H3 L2,4 Z M1.5,5 H6.5 V7.5 H1.5 Z" fill="var(--brand-blue)"/></svg>555-201-4410</li>
        <li><svg viewBox="0 0 8 8"><rect x="2" y="0.5" width="4" height="7" rx="0.6" fill="none" stroke="var(--brand-blue)" stroke-width="1"/></svg>555-201-4432</li>
        <li><svg viewBox="0 0 8 8"><rect x="2" y="1" width="4" height="2" fill="var(--brand-blue)"/><rect x="0.5" y="3.5" width="7" height="4" fill="var(--brand-blue)"/></svg>555-201-4458</li>
        <li><svg viewBox="0 0 8 8"><rect x="0.5" y="1.5" width="7" height="5" fill="var(--brand-blue)"/><path d="M0.5,1.5 L4,4.5 L7.5,1.5" fill="none" stroke="#fff" stroke-width="0.7"/></svg>hello@brightholdrealty.example</li>
        <li><svg viewBox="0 0 8 8"><circle cx="4" cy="4" r="3.5" fill="var(--brand-blue)"/><path d="M0.5,4 H7.5 M4,0.5 V7.5" stroke="#fff" stroke-width="0.6"/></svg>www.brightholdrealty.example</li>
      </ul>
    </div>

    <article class="letter">
      <p class="date">Cartagena de Indias, Ocober 12,2015</p>
      <p class="recipient">Sr.<br>MARCO RUIZ<br>Web Master<br>City</p>
      <div class="body">
        <p>Contrary to popular belief, Lorem Ipsum is not simply random text. It has roots in a piece of classical Latin literature from 45 BC, making it over 2000 years old. Daniel Ashford, a Latin professor at Larkfield College in Virginia, looked up one of the more obscure Latin words, consectetur, from a Lorem Ipsum passage, and going through the cites of the word in classical literature,</p>
        <p>discovered the undoubtable source. Lorem Ipsum comes from sections 1.10.32 and 1.10.33 of "de Finibus Bonorum et Malorum" (The Extremes of Good and Evil) by Aurelius Varro, written in 45 BC. This book is a treatise on the theory of ethics, very popular during the Renaissance. The first line of Lorem Ipsum, "Lorem ipsum dolor sit amet..", comes from a line in section 1.10.32.</p>
        <p>The standard chunk of Lorem Ipsum used since the 1500s is reproduced below for those interested. Sections 1.10.32 and 1.10.33 from "de Finibus Bonorum et Malorum" by Aurelius Varro are also reproduced in their exact original form, accompanied by English versions from the 1914 translation by H. Lowell.</p>
        <p>There are many variations of passages of Lorem Ipsum available, but the majority have suffered alteration in some form, by injected humour, or randomised words which don't look even slightly believable. If you are going to use a passage of Lorem Ipsum, you need to be sure there isn't anything embarrassing hidden in the middle of text.</p>
      </div>
    </article>

    <div class="signature" role="img" aria-label="Handwritten signature of the sender"></div>

    <div class="brand-band">
      <svg viewBox="0 0 521 10" preserveAspectRatio="none">
        <rect width="521" height="10" fill="var(--band-grey)"/>
        <polygon points="0,0 309,0 301,10 0,10" fill="var(--brand-blue)"/>
      </svg>
    </div>
  </section>

</div>
</body>
</html>
```